New Year's card HTML

can you produce a best new years wishes 2018 design in HTML for our website as what I would like to send by email towards my network of candidates / customers ...

It must be wow, inspiring , design, meaningfull... MMM those people care about me, or those people will help me to go the extra mile, to help me to achieve my career goals, Your best move, enhance my possibilities, bring the love back

Target Market(s)

CEo's / CMO's/ HRDirectors network of 450k

Coding

Coded - Design and coding required

Number of Pages Required

1 page

Colors

Designer to choose colors to be used in the design.

Requirements
Must have
• Logo / visual / website adress www.moravintel.com and a call to action
Should not have
• no sound as our business is confidential

```html
<!DOCTYPE html>
<html lang="en">
<head>
<meta charset="utf-8">
<title>Happy New Year 2018 – Moravintel</title>
<link rel="stylesheet" href="https://fonts.googleapis.com/css2?family=Quicksand:wght@700&family=Poppins:wght@400;600&family=Open+Sans:wght@700&display=swap">
<style>
  :root {
    --night-top: #03060f;
    --night-mid: #0b1a3e;
    --sky-glow: #2a5fa8;
    --city-teal: #1f7f95;
    --water-deep: #041624;
    --spark-blue: #5fd2ff;
    --spark-violet: #b460e6;
    --year-fill: #e2f1ff;
    --year-glow: #4aa8ff;
    --greeting-fill: #ffe9cf;
    --greeting-glow: #e0181c;
    --white: #ffffff;
  }
  * { margin: 0; padding: 0; box-sizing: border-box; }
  html, body { width: 1182px; height: 1200px; overflow: hidden; background: var(--night-top); }
  .card { position: relative; width: 1182px; height: 1200px; overflow: hidden; }

  .scene {
    position: absolute; inset: 0;
    background:
      radial-gradient(ellipse 260px 240px at 340px 560px, rgba(95,210,255,.55), transparent 70%),
      radial-gradient(ellipse 300px 260px at 920px 520px, rgba(180,96,230,.6), transparent 70%),
      radial-gradient(ellipse 220px 220px at 640px 250px, rgba(170,170,255,.4), transparent 70%),
      radial-gradient(ellipse 160px 180px at 170px 430px, rgba(90,150,255,.3), transparent 70%),
      linear-gradient(to bottom,
        var(--night-top) 0%,
        var(--night-mid) 35%,
        var(--sky-glow) 60%,
        #3a6fa8 68%,
        var(--city-teal) 78%,
        #0d3a52 84%,
        var(--water-deep) 100%);
  }

  .headline { position: absolute; left: 0; width: 100%; text-align: center; }
  .year {
    top: 300px;
    font-family: "Quicksand", sans-serif; font-weight: 700;
    font-size: 205px; line-height: 1; letter-spacing: 22px;
    color: var(--year-fill);
    text-shadow: 0 0 18px var(--year-glow), 0 0 40px var(--year-glow);
    padding-left: 0; margin-left: 0;
    transform: translateX(0);
  }
  .greeting {
    top: 505px;
    font-family: "Poppins", sans-serif; font-weight: 600;
    font-size: 96px; line-height: 1.1; letter-spacing: -2px;
    color: var(--greeting-fill);
    text-shadow: 0 0 6px var(--greeting-glow), 0 0 16px var(--greeting-glow), 2px 3px 4px #8a0000;
    left: -5px;
  }

  .brand {
    position: absolute; left: 53px; top: 1076px;
    display: flex; align-items: center; gap: 26px;
  }
  .brand-mark { width: 56px; height: 56px; border-radius: 50%; background: var(--white); }
  .brand-name {
    font-family: "Poppins", sans-serif; font-weight: 400;
    font-size: 46px; letter-spacing: 3px; color: var(--white);
  }

  .cta {
    position: absolute; left: 903px; top: 1068px;
    width: 215px; height: 65px;
    border: 2.5px solid var(--white); border-radius: 33px;
    display: flex; align-items: center; justify-content: center;
    font-family: "Open Sans", sans-serif; font-weight: 700; font-size: 19px;
    color: var(--white); text-decoration: none;
  }
</style>
</head>
<body>
  <main class="card">
    <div class="scene" role="img" aria-label="Blue, white and violet fireworks bursting over a lit city skyline at night, reflected in the river below"></div>

    <h1 class="headline year">2018</h1>
    <p class="headline greeting">Happy New Year</p>

    <div class="brand">
      <span class="brand-mark"></span>
      <span class="brand-name">MORAVINTEL</span>
    </div>

    <a class="cta" href="https://www.moravintel.com">VISIT OUR SITE</a>
  </main>
</body>
</html>
```